Brookvale Estates LLC stationary for a real estate property management company.

Create stationary (letterhead, envelopes, business cards) using Brookvale Estates LLC logo as primary creative element. Stationary design needs to be horizontal, leaving as much space as possible for correspondence copy. See attached Creative Brief and past stationary files for details.

Target Market(s)

Prospective apartment residents and current residents, vendors, and government agencies.

Industry/Entity Type

Property Management

Contact Information for Business Card

Business card employee title: Property Manager. Should include address, phone, fax, email, website, slogan, and Brookvale Estates logo.

Font styles to use
Sans Serif

Colors
0592cd
000000

Requirements
Must have
• Tone should be conservative, institutional, business (i.e. banking, finance, real estate). Must include: address, phone, fax, website, and slogan (see attached Creative Brief). Should be a horizontal design, leaving as much room as possible for letter correspondence copy.
Nice to have
• Please use an Arial or Helvetica style font.
Should not have
• Letterhead layout should leave as much room as possible for copy.

```html
<!DOCTYPE html>
<html lang="en">
<head>
<meta charset="utf-8">
<title>Brookvale Estates LLC – Business Card</title>
<link rel="stylesheet" href="https://fonts.googleapis.com/css2?family=Arimo:wght@400;700&display=swap">
<style>
  :root {
    --brand-blue: #0b6aa6;
    --brand-grey: #505050;
    --text-grey: #4a4a4a;
    --card-white: #f7f7f7;
    --backdrop: #e4e4e4;
    --card-shadow: rgba(0, 0, 0, 0.28);
  }
  * { margin: 0; padding: 0; box-sizing: border-box; }
  html, body { width: 1200px; height: 960px; overflow: hidden; }
  body {
    background: var(--backdrop);
    font-family: "Arimo", Arial, Helvetica, sans-serif;
    position: relative;
  }
  .card {
    position: absolute;
    width: 600px;
    height: 340px;
    background: var(--card-white);
    box-shadow: 0 3px 6px var(--card-shadow);
    overflow: hidden;
  }
  .card--front { left: 302px; top: 130px; }
  .card--back { left: 298px; top: 490px; }

  .front-circle {
    position: absolute;
    left: 298px;
    top: -20px;
    width: 380px;
    height: 380px;
    border-radius: 50%;
    background: var(--brand-blue);
  }

  .company-name {
    position: absolute;
    left: 36px;
    top: 36px;
  }
  .company-name__main {
    display: block;
    font-size: 44px;
    line-height: 46px;
    font-weight: 700;
    color: var(--brand-blue);
    white-space: nowrap;
  }
  .company-name__sub {
    display: block;
    font-size: 19px;
    line-height: 22px;
    font-weight: 700;
    color: var(--brand-grey);
    letter-spacing: 3px;
    white-space: nowrap;
  }
  .contact {
    position: absolute;
    left: 36px;
    top: 118px;
    color: var(--text-grey);
  }
  .contact__name {
    font-size: 20px;
    font-weight: 700;
    color: var(--brand-blue);
    line-height: 24px;
  }
  .contact__title {
    font-size: 15px;
    line-height: 20px;
    margin-bottom: 9px;
  }
  .contact__address {
    font-size: 13.5px;
    line-height: 18px;
    margin-bottom: 8px;
  }
  .contact__list { list-style: none; font-size: 13.5px; }
  .contact__list li {
    display: flex;
    align-items: center;
    height: 19.5px;
  }
  .contact__list svg {
    width: 12px;
    height: 12px;
    margin-right: 10px;
    fill: var(--brand-blue);
  }
  .slogan {
    margin-top: 6px;
    font-size: 14px;
    font-weight: 700;
    color: var(--brand-blue);
  }

  .back-name {
    position: absolute;
    left: 0;
    right: 0;
    top: 138px;
    text-align: center;
  }
  .back-name__main {
    display: block;
    font-size: 50px;
    line-height: 52px;
    font-weight: 700;
    color: var(--brand-blue);
  }
  .back-name__sub {
    display: block;
    font-size: 21px;
    line-height: 26px;
    font-weight: 700;
    color: var(--brand-grey);
    letter-spacing: 4px;
  }
</style>
</head>
<body>

<section class="card card--front" aria-label="Business card front">
  <div class="front-circle"></div>
  <div class="company-name">
    <span class="company-name__main">BROOKVALE</span>
    <span class="company-name__sub">ESTATES LLC</span>
  </div>
  <div class="contact">
    <p class="contact__name">DANIEL HARTWELL</p>
    <p class="contact__title">Property Manager</p>
    <p class="contact__address">2718 Linden Crest Avenue #B210<br>San Diego, CA 92108</p>
    <ul class="contact__list">
      <li>
        <svg viewBox="0 0 24 24" aria-hidden="true"><path d="M6.6 10.8a15.1 15.1 0 0 0 6.6 6.6l2.2-2.2c.3-.3.7-.4 1-.2 1.1.4 2.3.6 3.6.6.6 0 1 .4 1 1V20c0 .6-.4 1-1 1A17 17 0 0 1 3 4c0-.6.4-1 1-1h3.5c.6 0 1 .4 1 1 0 1.3.2 2.5.6 3.6.1.3 0 .7-.2 1z"/></svg>
        619-555-0142
      </li>
      <li>
        <svg viewBox="0 0 24 24" aria-hidden="true"><path d="M6 2h10l2 2v5H6zM3 10h18a1 1 0 0 1 1 1v8a1 1 0 0 1-1 1H3a1 1 0 0 1-1-1v-8a1 1 0 0 1 1-1zm3 3v2h4v-2zm7 0v2h2v-2zm3 0v2h2v-2z"/></svg>
        619-555-0187
      </li>
      <li>
        <svg viewBox="0 0 24 24" aria-hidden="true"><path d="M2 5h20v14H2zm2 2v.4l8 5.2 8-5.2V7zm0 2.8V17h16V9.8l-8 5.2z"/></svg>
        daniel@brookvaleestates.us
      </li>
      <li>
        <svg viewBox="0 0 24 24" aria-hidden="true"><path d="M12 2a10 10 0 1 0 0 20 10 10 0 0 0 0-20zm-1 17.9A8 8 0 0 1 4.2 10.2L9 15v1a2 2 0 0 0 2 2zm6.9-2.5A2 2 0 0 0 16 16h-1v-3a1 1 0 0 0-1-1H8v-2h2a1 1 0 0 0 1-1V7h2a2 2 0 0 0 2-2v-.4a8 8 0 0 1 2.9 12.8z"/></svg>
        www.brookvaleestates.us
      </li>
    </ul>
    <p class="slogan">Multifamily Property Management</p>
  </div>
</section>

<section class="card card--back" aria-label="Business card back">
  <div class="back-name">
    <span class="back-name__main">BROOKVALE</span>
    <span class="back-name__sub">ESTATES LLC</span>
  </div>
</section>

</body>
</html>
```